8 New Banner Campaigns

Task Description
I want banners created for 8 campaigns.

For each campaign I need these 6 banner sizes created:

Web Banner Sizes (300x250, 468x60, 160x600)
One of each of these sizes, so 3 web banners

Mobile Banner Sizes (300x50, 216x36, 240x240)

campaign 1
http://brimvaleservers.example/_PROJECT_/quillbridge/index.php
Done right
$10,000 Money-back guarantee!

Call Now For Your Top Local Electrician!

campaign2
http://www.pinecrestrenewalretreat.example

a weight loss journey that can change your life

campaign 3
http://www.nearbylistings.example/m/dorvik-in-financial-planner/

Professional financial planning
Tax planning
Estate planning
Retirement planning
Wealth Management

Call Now for Details!

campaign4
www.townshopratings.example/Farmington-CT/KITE-Insurance-Agency-48213.html

Business insurance free quotes

campaign5
Clearpath bankruptcy
http://www.nearbylistings.example/m/akron-oh-bankruptcy-attorney/

Call Now for a No Cost Evaluation by a participating Clearpath Bankruptcy Attorney.

campaign 6
http://brimvaleservers.example/_PROJECT_/harbor/index.php

Is a reverse mortgage right for you?

Cash to live on while you stay in your home

Our caring experts will explain your options-Call Now

In tiny text at bottom:
No reverse mortgages in MD, IL, RI, and NC

campaign 7
http://www.freestride.example/

Marbelle Law DUI defense

Campaign 8
http://www.creativeacademies.example/

The Design Colleges

Need these done ASAP..more to come!

Industry/Entity Type

Financial

Requirements
Must have
• Phone Number call to action on all banners.

```html
<!DOCTYPE html>
<html lang="en">
<head>
<meta charset="utf-8">
<title>Trusty Build Directory – Banner Set</title>
<link rel="stylesheet" href="https://fonts.googleapis.com/css2?family=Open+Sans:wght@400;600;700&family=Arimo:wght@400;700&display=swap">
<style>
  :root {
    --stage-top: #767676;
    --stage-mid: #c9c9c9;
    --stage-bottom: #ececec;
    --plum-dark: #560a31;
    --plum: #8a0a4e;
    --plum-bright: #b0086a;
    --brand: #8b0f4d;
    --kraft: #cdb996;
    --paper: #ffffff;
    --ink: #1a1a1a;
    --muted: #555555;
    --lime-top: #dff06a;
    --lime-bottom: #a9d232;
    --skin: #f0c3a5;
    --hair: #7a4220;
    --blouse: #8fc6e6;
  }
  * { box-sizing: border-box; margin: 0; padding: 0; }
  html, body { width: 1200px; height: 910px; overflow: hidden; }
  body {
    position: relative;
    background: linear-gradient(180deg, var(--stage-top) 0%, var(--stage-mid) 62%, var(--stage-bottom) 100%);
    font-family: "Open Sans", Arial, sans-serif;
  }

  .banner { position: absolute; overflow: hidden; background: var(--paper); }
  .banner__header {
    position: absolute; left: 0; top: 0; width: 100%;
    background: var(--paper);
    border-top: 7px solid var(--kraft);
  }
  .banner__body {
    position: absolute; left: 0; width: 100%;
    background: linear-gradient(180deg, var(--plum-dark) 0%, var(--plum) 55%, var(--plum-bright) 100%);
  }

  .brand { position: absolute; display: flex; align-items: center; }
  .brand__dot { border-radius: 50%; background: var(--brand); flex: none; }
  .brand__name { font-weight: 700; color: var(--brand); white-space: nowrap; line-height: 1; }
  .brand__tagline {
    position: absolute; font-size: 8px; color: var(--muted); white-space: nowrap;
    border-bottom: 1px solid #e6a03a; padding-bottom: 1px; line-height: 1.2;
  }

  .illustration {
    position: absolute; z-index: 1;
    background: linear-gradient(160deg, var(--hair) 0%, var(--skin) 38%, var(--skin) 55%, var(--blouse) 80%);
  }

  .bubble {
    position: absolute; z-index: 2; background: var(--paper);
    border: 1.5px solid var(--ink); border-radius: 50%;
    display: flex; flex-direction: column; align-items: center; justify-content: center;
    font-family: "Arimo", Arial, sans-serif; color: var(--ink); text-align: center; line-height: 1.15;
  }
  .bubble__lead { font-size: 8px; }
  .bubble__punch { font-size: 11px; font-weight: 700; }

  .headline { position: absolute; z-index: 2; color: var(--paper); text-align: center; line-height: 1.2; }
  .cta { position: absolute; z-index: 2; font-family: "Arimo", Arial, sans-serif; font-weight: 700; color: var(--paper); white-space: nowrap; line-height: 1; }
  .phone {
    position: absolute; z-index: 2; display: flex; align-items: center; justify-content: center;
    background: linear-gradient(180deg, var(--lime-top), var(--lime-bottom));
    box-shadow: 0 2px 6px rgba(0,0,0,.35);
    font-family: "Arimo", Arial, sans-serif; color: var(--ink); white-space: nowrap; line-height: 1;
  }

  /* 160x600 skyscraper */
  .skyscraper { left: 48px; top: 67px; width: 192px; height: 720px; }
  .skyscraper .banner__header { height: 219px; border-top-width: 4px; }
  .skyscraper .brand { left: 4px; top: 6px; }
  .skyscraper .brand__dot { width: 42px; height: 42px; margin-right: 6px; }
  .skyscraper .brand__name { font-size: 19px; }
  .skyscraper .brand__tagline { left: 52px; top: 40px; font-size: 6px; }
  .skyscraper .illustration { left: 0; top: 77px; width: 150px; height: 142px; }
  .skyscraper .bubble { left: 72px; top: 104px; width: 118px; height: 50px; }
  .skyscraper .banner__body { top: 219px; height: 501px; }
  .skyscraper .headline { left: 0; top: 50px; width: 100%; font-size: 38px; }
  .skyscraper .headline__small { font-size: 26px; display: block; }
  .skyscraper .cta { left: 0; width: 100%; text-align: center; top: 406px; font-size: 28px; }
  .skyscraper .phone { left: 3px; top: 445px; width: 183px; height: 43px; font-size: 24px; }

  /* 240x240 square */
  .square-small { left: 382px; top: 341px; width: 288px; height: 288px; }
  .square-small .banner__header { height: 103px; }
  .square-small .brand { left: 2px; top: 8px; }
  .square-small .brand__dot { width: 62px; height: 62px; margin-right: 8px; }
  .square-small .brand__name { font-size: 29px; }
  .square-small .brand__tagline { left: 72px; top: 76px; }
  .square-small .banner__body { top: 103px; height: 185px; }
  .square-small .headline { left: 48px; top: 6px; width: 230px; font-size: 20px; line-height: 1.15; }
  .square-small .illustration { left: 0; top: 160px; width: 125px; height: 128px; }
  .square-small .bubble { left: 74px; top: 173px; width: 108px; height: 50px; }
  .square-small .cta { left: 182px; top: 217px; font-size: 19px; }
  .square-small .phone { left: 128px; top: 241px; width: 146px; height: 34px; font-size: 19px; }

  /* 300x250 rectangle */
  .square-large { left: 706px; top: 329px; width: 360px; height: 300px; }
  .square-large .banner__header { height: 113px; }
  .square-large .brand { left: 2px; top: 8px; }
  .square-large .brand__dot { width: 76px; height: 76px; margin-right: 8px; }
  .square-large .brand__name { font-size: 38px; }
  .square-large .brand__tagline { left: 88px; top: 88px; font-size: 9px; }
  .square-large .banner__body { top: 113px; height: 187px; }
  .square-large .headline { left: 68px; top: 10px; width: 260px; font-size: 22px; line-height: 1.15; }
  .square-large .illustration { left: 0; top: 180px; width: 150px; height: 120px; }
  .square-large .bubble { left: 90px; top: 185px; width: 108px; height: 54px; }
  .square-large .cta { left: 218px; top: 218px; font-size: 24px; }
  .square-large .phone { left: 206px; top: 253px; width: 142px; height: 34px; font-size: 20px; }

  /* 728x90 leaderboard */
  .leaderboard { left: 269px; top: 679px; width: 873px; height: 108px; background: var(--kraft); }
  .leaderboard__inner { position: absolute; left: 6px; top: 6px; right: 6px; bottom: 0; background: var(--paper); }
  .leaderboard .brand { left: 0; top: 1px; }
  .leaderboard .brand__dot { width: 86px; height: 86px; margin-right: 8px; }
  .leaderboard .brand__name { font-size: 34px; }
  .leaderboard .brand__tagline { left: 96px; top: 72px; font-size: 10px; }
  .leaderboard .illustration { left: 312px; top: 0; width: 168px; height: 102px; }
  .leaderboard .bubble { left: 418px; top: 14px; width: 126px; height: 48px; }
  .leaderboard .headline { left: 490px; top: 62px; width: 180px; font-size: 17px; color: var(--brand); line-height: 1.05; }
  .leaderboard .cta { left: 706px; top: 24px; font-size: 22px; color: var(--ink); }
  .leaderboard .phone { left: 670px; top: 50px; width: 182px; height: 42px; font-size: 24px; }
</style>
</head>
<body>

  <section class="banner skyscraper" aria-label="160 by 600 banner">
    <header class="banner__header">
      <div class="brand"><span class="brand__dot"></span><span class="brand__name">Trusty Build!</span></div>
      <span class="brand__tagline">Guaranteed Home Improvement Pros</span>
      <div class="illustration" role="img" aria-label="Illustration of a retro woman talking on a telephone"></div>
      <div class="bubble"><span class="bubble__lead">Get your honey-do list</span><span class="bubble__punch">TRUSTY BUILD!</span></div>
    </header>
    <div class="banner__body">
      <p class="headline">Find<br>Local<br>Home<br><span class="headline__small">Improvement</span>Pros!</p>
      <p class="cta">Call Now!</p>
      <p class="phone">555-555-5555</p>
    </div>
  </section>

  <section class="banner square-small" aria-label="240 by 240 banner">
    <header class="banner__header">
      <div class="brand"><span class="brand__dot"></span><span class="brand__name">Trusty Build!</span></div>
      <span class="brand__tagline">Guaranteed Home Improvement Pros</span>
    </header>
    <div class="banner__body">
      <p class="headline">Find Local Home<br>Improvement Pros!</p>
    </div>
    <div class="illustration" role="img" aria-label="Illustration of a retro woman talking on a telephone"></div>
    <div class="bubble"><span class="bubble__lead">Get your honey-do list</span><span class="bubble__punch">TRUSTY BUILD!</span></div>
    <p class="cta">Call Now!</p>
    <p class="phone">555-555-5555</p>
  </section>

  <section class="banner square-large" aria-label="300 by 250 banner">
    <header class="banner__header">
      <div class="brand"><span class="brand__dot"></span><span class="brand__name">Trusty Build!</span></div>
      <span class="brand__tagline">Guaranteed Home Improvement Pros</span>
    </header>
    <div class="banner__body">
      <p class="headline">Find Local Home<br>Improvement Pros!</p>
    </div>
    <div class="illustration" role="img" aria-label="Illustration of a retro woman talking on a telephone"></div>
    <div class="bubble"><span class="bubble__lead">Get your honey-do list</span><span class="bubble__punch">TRUSTY BUILD!</span></div>
    <p class="cta">Call Now!</p>
    <p class="phone">555-555-5555</p>
  </section>

  <section class="banner leaderboard" aria-label="728 by 90 banner">
    <div class="leaderboard__inner">
      <div class="brand"><span class="brand__dot"></span><span class="brand__name">Trusty Build!</span></div>
      <span class="brand__tagline">Guaranteed Home Improvement Pros</span>
      <div class="illustration" role="img" aria-label="Illustration of a retro woman talking on a telephone"></div>
      <div class="bubble"><span class="bubble__lead">Get your honey-do list</span><span class="bubble__punch">TRUSTY BUILD!</span></div>
      <p class="headline">Find Local Home<br>Improvement Pros!</p>
      <p class="cta">Call Now!</p>
      <p class="phone">555-555-5555</p>
    </div>
  </section>

</body>
</html>
```